Commercial Swimming Pool - Design-Build Contractor Website Design

I need a new website that will feature our newly developed logo and trade name as well as provide a fully updated site experience. We are not a residential builder - we strictly design and install high-end commercial pools. I need the website to highlight our portfolio and communicate the various types of projects in which we specialize. I want the effect of the site to reflect the high-end nature of our services - projects like the 57th floor spa at the Phila Silver Willow, the aquatic therapy portion of the Phila Ravenhawks training facility, a 5om indoor competition pool for the prestigious Dallowmere Academy, the indoor water park at The Quenwick Lodge or the recent country club renovation projects we've completed in our region (to name a few examples).
Need extra days to review

```html
<!DOCTYPE html>
<html lang="en">
<head>
<meta charset="utf-8">
<title>Corvane Aquatics – Commercial Pool Design-Build</title>
<link href="https://fonts.googleapis.com/css2?family=Josefin+Sans:wght@600;700&family=Roboto:wght@400;500;700&display=swap" rel="stylesheet">
<style>
:root{
  --navy:#1b2450;
  --navy-deep:#131a3d;
  --blue:#3fb3e6;
  --ink:#1d1d1f;
  --text:#3d3d3d;
  --muted:#8a8f99;
  --line:#c9ccd2;
  --light-bg:#f3f3f3;
  --white:#ffffff;
  --head:"Josefin Sans", sans-serif;
  --body:"Roboto", sans-serif;
}
*{box-sizing:border-box;margin:0;padding:0}
html,body{width:1200px;height:3787px;overflow:hidden;background:var(--white)}
body{font-family:var(--body);color:var(--text)}
.page{position:relative;width:1200px;height:3787px;overflow:hidden}
.abs{position:absolute}
a{color:inherit;text-decoration:none}

/* top bar */
.topbar{left:0;top:0;width:1200px;height:43px;background:var(--navy)}
.topbar-mail{left:123px;top:12px;color:var(--white);font-size:15px;display:flex;align-items:center;gap:9px}
.social-dots{left:794px;top:9px;display:flex;gap:8px}
.social-dots span{width:25px;height:25px;border-radius:50%;background:var(--white);display:block}
.topbar-quote{left:929px;top:12px;color:var(--white);font-family:var(--head);font-weight:700;font-size:16px;display:flex;gap:8px;align-items:center}

/* nav */
.navbar{left:0;top:43px;width:1200px;height:64px;background:var(--white);box-shadow:0 1px 4px rgba(0,0,0,.06)}
.nav-link{font-size:15px;color:var(--ink)}
.nav-link.active{color:var(--blue)}
.nav-link.active::after{content:"";position:absolute;left:0;right:0;top:33px;height:2px;background:var(--blue)}
.brand-box{left:457px;top:0;width:287px;height:122px;background:var(--white);border-radius:0 0 14px 14px;box-shadow:0 2px 8px rgba(0,0,0,.08);display:flex;align-items:center;justify-content:center;gap:10px}
.brand-mark{width:26px;height:26px;border-radius:50%;background:var(--blue)}
.brand-name{font-family:var(--head);font-weight:700;font-size:27px;color:var(--navy);letter-spacing:.5px;line-height:1}

/* hero */
.hero{left:0;top:107px;width:1200px;height:620px}
.hero-kicker{left:110px;top:248px;font-family:var(--head);font-weight:700;font-size:30px;color:var(--white);letter-spacing:1px}
.hero-title{left:108px;top:292px;font-family:var(--head);font-weight:700;font-size:90px;line-height:92px;color:var(--white);letter-spacing:1px}
.btn-pill{background:var(--blue);color:var(--white);font-family:var(--head);font-weight:700;display:flex;align-items:center;justify-content:center;border-radius:0 24px 24px 24px}
.hero-btn{left:113px;top:498px;width:152px;height:50px;font-size:14px;letter-spacing:.5px}

/* section titles */
.section-title{left:0;width:1200px;text-align:center;font-family:var(--head);font-weight:700;font-size:35px;color:var(--ink);letter-spacing:1px}

/* project cards */
.card{background:var(--white);box-shadow:0 4px 22px rgba(0,0,0,.12)}
.card-photo{position:absolute;left:0;top:0;width:100%}
.card-body{position:absolute;left:20px;right:16px}
.card-title{font-family:var(--head);font-weight:700;color:var(--ink);font-size:20px;line-height:29px}
.card-link{margin-top:16px;display:flex;align-items:center;gap:8px;font-family:var(--head);font-weight:700;color:var(--blue);font-size:15px}
.card.feature .card-title{font-size:23px;line-height:34px}
.slider-arrow{width:24px;height:24px;border-radius:50%;display:flex;align-items:center;justify-content:center}
.slider-arrow.prev{background:var(--navy)}
.slider-arrow.next{background:var(--blue)}

/* about */
.about{left:0;top:1490px;width:1200px;height:451px;background:linear-gradient(90deg,#1b2652 0%,#243769 38%,#3f6f95 60%,#7fb2c9 80%,#9ccbd8 100%)}
.about-title{left:115px;top:1553px;font-family:var(--head);font-weight:700;font-size:35px;color:var(--white);letter-spacing:.5px}
.about-text{left:115px;top:1610px;width:460px;font-size:14.5px;line-height:26px;color:var(--white)}
.about-btn{left:115px;top:1815px;width:147px;height:50px;font-size:15px}

/* portfolio */
.tile{position:absolute}

/* contact */
.contact{left:0;top:2853px;width:1200px;height:545px;background:var(--light-bg)}
.contact-title{left:110px;top:2962px;font-family:var(--head);font-weight:700;font-size:35px;color:var(--ink);letter-spacing:.5px}
.contact-text{left:110px;top:3016px;width:365px;font-size:14.5px;line-height:26px;color:var(--text)}
.contact-item{left:110px;display:flex;gap:16px;font-size:14.5px;line-height:26px;color:var(--text)}
.contact-item.mail{color:var(--blue)}
.quote-card{left:507px;top:2935px;width:577px;height:368px;background:var(--white);border-radius:6px;box-shadow:0 2px 16px rgba(0,0,0,.07)}
.quote-title{left:540px;top:2973px;font-family:var(--head);font-weight:700;font-size:27px;color:var(--ink);letter-spacing:.5px}
.field{border:1px solid var(--line);border-radius:3px;font-size:14.5px;color:var(--muted);padding:10px 14px}
.send-btn{left:540px;top:3221px;width:511px;height:41px;background:var(--navy);color:var(--white);font-size:15px;font-weight:700;display:flex;align-items:center;justify-content:center;border-radius:3px;letter-spacing:.3px}

/* footer */
.footer{left:0;top:3400px;width:1200px;height:387px;background:var(--navy-deep);border-top-right-radius:130px}
.footer-brand{left:107px;top:3474px;display:flex;align-items:center;gap:10px}
.footer-brand .brand-name{color:var(--white);font-size:27px}
.footer-social{left:184px;top:3562px;display:flex;gap:13px}
.footer-social span{width:12px;height:12px;border-radius:2px;background:var(--blue);display:block}
.footer-head{font-family:var(--head);font-weight:700;font-size:20px;color:var(--white);letter-spacing:.3px}
.footer-list{list-style:none;font-size:14.5px;color:var(--white)}
.footer-list li{height:30px;line-height:30px}
.news-input{left:765px;top:3500px;width:241px;height:28px;border-bottom:1px solid #4a5070;border-left:2px solid var(--white);padding-left:14px;font-size:14px;color:#6b7190;line-height:26px}
.news-btn{left:762px;top:3560px;width:122px;height:36px;background:var(--blue);color:var(--white);border-radius:18px;font-size:15px;font-weight:500;display:flex;align-items:center;justify-content:center}
.footer-rule{left:108px;top:3700px;width:980px;height:1px;background:#2c3356}
.copyright{left:0;top:3731px;width:1200px;text-align:center;font-size:14.5px;color:var(--white)}
</style>
</head>
<body>
<div class="page">

  <!-- top bar -->
  <div class="abs topbar"></div>
  <div class="abs topbar-mail">
    <svg width="14" height="11" viewBox="0 0 14 11"><rect x="0.5" y="0.5" width="13" height="10" rx="1" fill="#fff"/><path d="M1 1l6 5 6-5" stroke="#1b2450" stroke-width="1.3" fill="none"/></svg>
    info@corvaneaquatics.com
  </div>
  <div class="abs social-dots" aria-label="Social links"><span></span><span></span><span></span></div>
  <div class="abs topbar-quote">
    <svg width="11" height="14" viewBox="0 0 11 14"><path d="M0 0h7l4 4v10H0z" fill="#fff"/><path d="M2 7h7M2 10h7" stroke="#1b2450" stroke-width="1.2"/></svg>
    Get a Quote
  </div>

  <!-- navigation -->
  <div class="abs navbar"></div>
  <a class="abs nav-link active" style="left:143px;top:64px">Home</a>
  <a class="abs nav-link" style="left:218px;top:64px">About Us</a>
  <a class="abs nav-link" style="left:317px;top:64px">Our Services</a>
  <a class="abs nav-link" style="left:789px;top:68px">Contact</a>
  <a class="abs nav-link" style="left:890px;top:68px">Projects</a>
  <a class="abs nav-link" style="left:997px;top:68px">Portfolio</a>
  <div class="abs brand-box"><span class="brand-mark"></span><span class="brand-name">CORVANE<br>AQUATICS</span></div>

  <!-- hero -->
  <svg class="abs hero" viewBox="0 0 1200 620" role="img" aria-label="Outdoor rectangular pool surrounded by trees and a stone deck">
    <defs>
      <linearGradient id="heroFill" x1="0" y1="0" x2="0" y2="1">
        <stop offset="0" stop-color="#34502f"/>
        <stop offset=".35" stop-color="#4f7a45"/>
        <stop offset=".5" stop-color="#7a7a6c"/>
        <stop offset=".62" stop-color="#3fc4d4"/>
        <stop offset="1" stop-color="#1d9fbf"/>
      </linearGradient>
    </defs>
    <path d="M0 420 C0 540 70 620 190 620 L1088 620 L1088 603 L0 603 Z" fill="#3fb3e6"/>
    <path d="M0 0 H1200 V600 H180 C70 600 0 540 0 430 Z" fill="url(#heroFill)"/>
  </svg>
  <div class="abs hero-kicker">WELCOME TO</div>
  <div class="abs hero-title">CORVANE<br>AQUATICS</div>
  <a class="abs btn-pill hero-btn">GET STARTED</a>

  <!-- projects -->
  <h2 class="abs section-title" style="top:810px">OUR PROJECTS</h2>

  <div class="abs slider-arrow prev" style="left:53px;top:1097px"><svg width="8" height="10" viewBox="0 0 8 10"><path d="M6 1L2 5l4 4" stroke="#fff" stroke-width="1.8" fill="none"/></svg></div>
  <div class="abs slider-arrow next" style="left:1128px;top:1097px"><svg width="8" height="10" viewBox="0 0 8 10"><path d="M2 1l4 4-4 4" stroke="#fff" stroke-width="1.8" fill="none"/></svg></div>

  <article class="abs card" style="left:115px;top:935px;width:295px;height:405px">
    <div class="card-photo" role="img" aria-label="Rooftop infinity spa edge with timber deck" style="height:268px;background:linear-gradient(180deg,#5aa5dc 0%,#8ec8e8 30%,#3d8a3a 42%,#1fb6e0 55%,#1aa5d4 68%,#8a5a44 72%,#6e4536 100%)"></div>
    <div class="card-body" style="top:285px">
      <h3 class="card-title">57th floor spa at the Phila Silver Willow</h3>
      <div class="card-link">Learn More <svg width="12" height="12" viewBox="0 0 12 12"><circle cx="6" cy="6" r="6" fill="#3fb3e6"/><path d="M5 3.5L7.5 6 5 8.5" stroke="#fff" stroke-width="1.5" fill="none"/></svg></div>
    </div>
  </article>

  <article class="abs card feature" style="left:431px;top:903px;width:340px;height:494px">
    <div class="card-photo" role="img" aria-label="Pool ladder rails in sparkling blue water under the sun" style="height:309px;background:linear-gradient(180deg,#3e7ec8 0%,#9ad0f0 40%,#5fb1e3 52%,#2376c2 100%)"></div>
    <div class="card-body" style="top:330px;left:23px">
      <h3 class="card-title">the aquatic therapy portion of the Phila Ravenhawks training facility,</h3>
      <div class="card-link">Learn More <svg width="13" height="13" viewBox="0 0 12 12"><circle cx="6" cy="6" r="6" fill="#3fb3e6"/><path d="M5 3.5L7.5 6 5 8.5" stroke="#fff" stroke-width="1.5" fill="none"/></svg></div>
    </div>
  </article>

  <article class="abs card" style="left:791px;top:935px;width:297px;height:431px">
    <div class="card-photo" role="img" aria-label="Outdoor pool with paved surround, trees and blue sky" style="height:268px;background:linear-gradient(180deg,#3c7fcc 0%,#a9cfee 32%,#3f6b3a 45%,#2a8ee0 58%,#d9b4a0 66%,#c9a08c 100%)"></div>
    <div class="card-body" style="top:285px">
      <h3 class="card-title">a 5om indoor competition pool for the prestigious Dallowmere Academy</h3>
      <div class="card-link">Learn More <svg width="12" height="12" viewBox="0 0 12 12"><circle cx="6" cy="6" r="6" fill="#3fb3e6"/><path d="M5 3.5L7.5 6 5 8.5" stroke="#fff" stroke-width="1.5" fill="none"/></svg></div>
    </div>
  </article>

  <!-- about -->
  <section class="abs about" role="img" aria-label="Swimmer in a sun hat resting at the edge of a pool"></section>
  <h2 class="abs about-title">ABOUT CORVANE AQUATICS.</h2>
  <p class="abs about-text">Lorem ipsum dolor sit amet, consectetur adipiscing elit, sed do eiusmod tempor incididunt ut labore et dolore magna aliqua. Quis ipsum suspendisse ultrices gravida. Risus commodo viverra maecenas accumsan lacus vel facilisis. Lorem ipsum dolor sit amet, consectetur adipiscing elit, sed do eiusmod tempor incididunt ut labore et dolore magna aliqua. Quis ipsum suspendisse ultrices gravida.</p>
  <a class="abs btn-pill about-btn">Learn More</a>

  <!-- portfolio -->
  <h2 class="abs section-title" style="top:2015px">PORTFOLIO</h2>
  <div class="tile" role="img" aria-label="Infinity edge pool overlooking the sea with timber deck" style="left:115px;top:2103px;width:247px;height:322px;background:linear-gradient(180deg,#dfe6ee 0%,#c3d3e2 35%,#3f86c4 55%,#2a6fb1 73%,#b07a4c 76%,#935f38 100%)"></div>
  <div class="tile" role="img" aria-label="Pool ladder beside wooden decking" style="left:369px;top:2103px;width:247px;height:322px;background:linear-gradient(135deg,#a8683f 0%,#8a4f2e 45%,#1c86d2 55%,#2a9be0 100%)"></div>
  <div class="tile" role="img" aria-label="Resort pool lined with palm trees" style="left:619px;top:2103px;width:468px;height:322px;background:linear-gradient(180deg,#3e6fb6 0%,#7fa8d8 30%,#3d5f3d 45%,#2aa4c6 60%,#1590b4 100%)"></div>
  <div class="tile" role="img" aria-label="Pool with steel ladder and tiled edge" style="left:116px;top:2429px;width:468px;height:322px;background:linear-gradient(180deg,#b9c3c5 0%,#5f8060 20%,#36a6c5 45%,#65c6d8 75%,#d9dfe2 100%)"></div>
  <div class="tile" role="img" aria-label="Hilltop pool under a bright sun" style="left:587px;top:2429px;width:247px;height:322px;background:linear-gradient(180deg,#2b6cc8 0%,#8dbbec 40%,#5f7a5a 52%,#33a9d8 66%,#8a5a44 80%,#6b4534 100%)"></div>
  <div class="tile" role="img" aria-label="Palm-lined pool with umbrellas at sunset" style="left:841px;top:2429px;width:247px;height:322px;background:linear-gradient(180deg,#e8c98a 0%,#f1dca8 30%,#7b8a4e 48%,#d9b36a 60%,#2fa7c4 75%,#1c86a8 100%)"></div>

  <!-- contact -->
  <section class="abs contact"></section>
  <h2 class="abs contact-title">CONTACT US</h2>
  <p class="abs contact-text">Lorem ipsum dolor sit amet, consectetur adipiscing elit, sed do eiusmod tempor incididunt ut labore et dolore magna aliqua. Quis ipsum suspendisse ultrices gravida. Risus commodo viverra maecenas accumsan lacus vel facilisis. Lorem ipsum dolor sit amet, consectetur adipiscing elit</p>
  <div class="abs contact-item" style="top:3200px">
    <svg width="28" height="36" viewBox="0 0 28 36"><path d="M14 2C7.4 2 2.5 7 2.5 13.3 2.5 22 14 34 14 34s11.5-12 11.5-20.7C25.5 7 20.6 2 14 2z" fill="none" stroke="#3fb3e6" stroke-width="1.6"/><circle cx="14" cy="13" r="4.5" fill="none" stroke="#3fb3e6" stroke-width="1.6"/></svg>
    <span style="color:var(--text)">12b Corvane Aquatics Lorem ipsum<br>dolor sit amet, consectetur</span>
  </div>
  <div class="abs contact-item mail" style="top:3266px">
    <svg width="30" height="22" viewBox="0 0 30 22"><rect x="1" y="1" width="28" height="20" fill="none" stroke="#3fb3e6" stroke-width="1.5"/><path d="M1 1l14 11L29 1M1 21l10-9M29 21l-10-9" fill="none" stroke="#3fb3e6" stroke-width="1.5"/></svg>
    <span>info@corvaneaquatics.com</span>
  </div>

  <div class="abs quote-card"></div>
  <h3 class="abs quote-title">GET A QUOTE</h3>
  <div class="abs field" style="left:540px;top:3027px;width:243px;height:41px">Name</div>
  <div class="abs field" style="left:540px;top:3091px;width:243px;height:41px">Email</div>
  <div class="abs field" style="left:540px;top:3156px;width:243px;height:41px">Phone</div>
  <div class="abs field" style="left:809px;top:3027px;width:243px;height:170px">Type Your Message</div>
  <a class="abs send-btn">SEND MESSAGE</a>

  <!-- footer -->
  <svg class="abs" style="left:0;top:3380px" width="1200" height="160" viewBox="0 0 1200 160" aria-hidden="true">
    <path d="M110 0 H1060 C1140 0 1200 50 1200 120 V160 H130 L130 20 Z" fill="#3fb3e6"/>
  </svg>
  <footer class="abs footer"></footer>
  <div class="abs footer-brand"><span class="brand-mark"></span><span class="brand-name">CORVANE<br>AQUATICS</span></div>
  <div class="abs footer-social" aria-label="Social links"><span></span><span></span><span></span><span></span></div>

  <h4 class="abs footer-head" style="left:410px;top:3455px">QUICK LINK</h4>
  <ul class="abs footer-list" style="left:413px;top:3489px">
    <li>Home</li><li>About Us</li><li>Our Services</li><li>Contact</li><li>Projects</li><li>Portfolio</li>
  </ul>
  <h4 class="abs footer-head" style="left:590px;top:3455px">SUPPORT</h4>
  <ul class="abs footer-list" style="left:594px;top:3489px">
    <li>Terms&amp;condtions</li><li>Privacy Policy</li><li>About Us</li><li>Support</li>
  </ul>
  <h4 class="abs footer-head" style="left:760px;top:3455px">SUBSCRIBE TO OUR NEWSLETTER</h4>
  <div class="abs news-input">Enter Your Email</div>
  <a class="abs news-btn">Subscribe</a>

  <div class="abs footer-rule"></div>
  <p class="abs copyright">©Copyrights 2023 Corvane Aquatics |&nbsp;&nbsp;&nbsp;All Rights Reserved</p>

</div>
</body>
</html>
```